International professional tennis coach needs a book cover design

This is my 2nd published book, the first one was a #1 on the best seller. I'm looking for a world class book cover design for this new book. The name of my first book was 5 Baseline Habits to Unlock Your Flow Rhythm, located on Bookvale.com

The title of the new book:

Title: The Craft of Rally Mastery
Subtitle: Developing a Strategic Advantage through Competitive Intelligence

I'm uploading our new CRAFT OF RALLY logo that I'd like for you to use as the centerpiece of the book design along with a 21st century design feel that incorporates what the book topic is below::

--> This book is about building competitive intelligence by using tennis data analytics to develop and expand a player's strategic advantage for match play. <--

The colors we would like to use are Blue, Yellow, and Green. These shades of these colors should be bold! (You will see the bold color examples of blues, yellows, and greens that I'm talking about in the logos that are attached here, especially the colors for my Racket GridDrill App logo.

I will upload the Racket GridDrill logo which should go somewhere on the back cover design (small size maybe in the bottom corner).

This book is revolutionary to the standard way of teaching tennis, it is based on a decade of recording and gathering tennis data analytics and then we created on-court practice games to develop better decision making in players for the competitive edge.

My websites are www.elevatedrillzone.com and www.craftofrallymastery.com

```html
<!DOCTYPE html>
<html lang="en">
<head>
<meta charset="utf-8">
<title>The Craft of Rally Mastery – Book Cover</title>
<link rel="stylesheet" href="https://fonts.googleapis.com/css2?family=Oswald:wght@200;500;700&family=Open+Sans:wght@400;600&display=swap">
<style>
  :root {
    --canvas-bg: #f1f2f1;
    --cover-green: #03924f;
    --accent-yellow: #f6bb10;
    --accent-blue: #0b72bd;
    --ink-white: #ffffff;
    --photo-warm: #8a7a6a;
    --photo-cool: #5d7288;
  }
  * { margin: 0; padding: 0; box-sizing: border-box; }
  html, body {
    width: 1200px; height: 1200px; overflow: hidden;
    background: var(--canvas-bg);
  }
  .canvas {
    position: relative; width: 1200px; height: 1200px;
    display: flex; justify-content: center; align-items: center; gap: 40px;
  }
  .cover {
    width: 520px; height: 840px;
    background: var(--cover-green);
    color: var(--ink-white);
    box-shadow: 0 10px 30px rgba(0,0,0,0.18);
  }

  /* Front cover */
  .front {
    display: flex; flex-direction: column; align-items: center;
    padding: 60px 40px 54px;
    font-family: "Oswald", sans-serif;
    text-align: center;
  }
  .front-title { display: flex; flex-direction: column; align-items: center; line-height: 0.92; }
  .title-lead { font-weight: 200; font-size: 78px; letter-spacing: -1px; }
  .title-key { font-weight: 700; font-size: 156px; color: var(--accent-yellow); letter-spacing: -2px; }
  .title-tail { font-weight: 700; font-size: 118px; letter-spacing: -1px; }

  .brand-mark {
    margin-top: 54px;
    display: flex; align-items: center; gap: 16px;
    font-family: "Oswald", sans-serif; font-weight: 700;
    font-size: 40px; color: var(--accent-yellow); letter-spacing: 1px;
  }
  .brand-dot {
    width: 30px; height: 30px; border-radius: 50%;
    background: var(--accent-blue);
  }

  .subtitle {
    margin-top: auto;
    font-family: "Open Sans", sans-serif; font-weight: 400;
    font-size: 23px; line-height: 1.35; letter-spacing: 0.5px;
    padding: 12px 0;
    border-top: 1px solid var(--accent-yellow);
    border-bottom: 1px solid var(--accent-yellow);
    width: 440px;
  }
  .front-authors {
    margin-top: 44px;
    font-weight: 500; font-size: 38px; letter-spacing: 0.5px;
  }

  /* Back cover */
  .back {
    display: flex; flex-direction: column;
    padding: 38px 34px 28px;
    font-family: "Open Sans", sans-serif;
  }
  .back-title {
    font-family: "Oswald", sans-serif; font-size: 30px; text-align: center;
    letter-spacing: -0.5px;
  }
  .back-title .lead { font-weight: 200; }
  .back-title .key { font-weight: 700; color: var(--accent-yellow); }
  .back-title .tail { font-weight: 500; }
  .blurb { margin-top: 16px; font-size: 10.4px; line-height: 1.42; text-align: justify; }
  .blurb p + p { margin-top: 3px; }
  .divider {
    height: 1px; margin: 14px 50px 10px;
    background: linear-gradient(90deg, transparent, var(--accent-yellow), transparent);
  }
  .author-name {
    font-family: "Oswald", sans-serif; font-weight: 500; font-size: 26px;
    color: var(--accent-yellow); text-align: center; letter-spacing: 0.5px;
  }
  .author-row { display: flex; gap: 12px; margin-top: 8px; }
  .author-photo { flex: 0 0 78px; height: 104px; }
  .author-photo.warm { background: linear-gradient(160deg, var(--photo-cool), var(--photo-warm)); }
  .author-photo.cool { background: linear-gradient(160deg, #7f9bb3, var(--photo-cool)); }
  .author-bio { font-size: 9.6px; line-height: 1.4; text-align: justify; }
  .back-footer {
    margin-top: auto; display: flex; align-items: center; gap: 8px;
    font-family: "Open Sans", sans-serif; font-weight: 600; font-size: 12px;
  }
  .footer-dot { width: 14px; height: 14px; border-radius: 50%; background: var(--ink-white); }
</style>
</head>
<body>
<main class="canvas">

  <section class="cover front" aria-label="Front cover">
    <h1 class="front-title">
      <span class="title-lead">THE CRAFT OF</span>
      <span class="title-key">RALLY</span>
      <span class="title-tail">MASTERY</span>
    </h1>
    <div class="brand-mark">
      <span class="brand-dot"></span>
      <span>CRAFT OF RALLY</span>
    </div>
    <p class="subtitle">Developing a Strategic Advantage<br>through Competitive Intelligence</p>
    <p class="front-authors">CORWIN ASHBY &amp; MILO FENWICK</p>
  </section>

  <section class="cover back" aria-label="Back cover">
    <h2 class="back-title"><span class="lead">THE CRAFT OF </span><span class="key">RALLY</span><span class="tail"> MASTERY</span></h2>
    <div class="blurb">
      <p>A practical guide on how to win more matches by becoming a more efficient and effective competitor.</p>
      <p>As a tennis player you have the ability to play better matches and win more of them. The Craft of Rally Mastery gives you a system to improve. We start with the individual game of the set itself. Our system examines your physical and mental progression, enabling you to upgrade your movement and performance from shot to shot and point to point. Our system seamlessly integrates the technical (physical) aspects with the tactical (mental/emotional) components, providing a comprehensive approach to elevate this performance. We aim to give you much more than how to hit great shots. Irrespective of your current skill level, we will provide you with a detailed strategic and tactical plan to enhance your performance, leading to improved results and increased success in your matches.</p>
      <p>The Craft of Rally Mastery emphasizes the importance of shifting focus from oneself to the opponent, encouraging players to analyze and understand their adversaries. By bringing the opponent back to the forefront of their thinking, the player creates the best possible context in which to improve as a competitor. In this book, we present a groundbreaking approach to tennis data analytics that seamlessly integrates match performance with practice sessions, and vice versa.</p>
    </div>

    <div class="divider"></div>
    <h3 class="author-name">CORWIN ASHBY</h3>
    <div class="author-row">
      <div class="author-photo warm" role="img" aria-label="Portrait photo of author Corwin Ashby"></div>
      <p class="author-bio">Corwin Ashby is regarded as one of the leading strategy and tactical coaches in the world today. He is the Creator of Racket GridDrill, the world's first Tennis Tracking App that maps and charts match play based on the rally length of a point. Corwin is a Best Selling Author of the book "5 Baseline Habits to Unlock Your Flow Rhythm" and the Co-Founder of The Craft of Rally Mastery promoting coach, player, and parent development. He is often sought after by coaches around the world to design the practice court in a way that revolutionizes a player's mindset to successfully negotiate the pressures of competitive match play.</p>
    </div>

    <div class="divider"></div>
    <h3 class="author-name">MILO FENWICK</h3>
    <div class="author-row">
      <div class="author-photo cool" role="img" aria-label="Portrait photo of author Milo Fenwick"></div>
      <p class="author-bio">Milo Fenwick is a writer and tennis coach. He is a Co-Founder at The Craft of Rally Mastery and has been working to create a theoretical framework for tennis players of all levels to improve. Milo studies the forces that act on the player during a tennis match (both internal and external) and works with players to meet the challenge these forces represent. He runs online and on court programs designed specifically to improve a player's Competitive Intelligence.</p>
    </div>

    <div class="back-footer">
      <span class="footer-dot"></span>
      <span>Racket GridDrill</span>
    </div>
  </section>

</main>
</body>
</html>
```